Packing for Razor Blade VELUMOR

Dears: We need a packing design. The product is an Disposable Razor Blade. We are a company in Brazil.

The packing consists in a bag package which the Disposables Razos are placed. 5 units into each bag.

The bag is not 100% printed and should let a space to the customer see the razors inside. Some competitors uses oval circle. I attached competitor package (Dax Marino)

The background color should be blue, this color tonality should vary its magnitude from dark blue to soft blue. Blue is a good color for personal care products because customer can take the impression of cleanness, especially for razor blade which has the fuction to shave.

You can feel free to add other colors however it can not be much colorfull because it may get trouble to printer company print it. Silver is good.

You can feel free to do details. You can feel free also to place the logo above the package or at bottom of it.

Dimmensions:
Heigh 24cm
Width 10cm

Featuring
- Featuring: Handle with Grip. In Portuguese - (Cabo Aderente)
- Featuring: 2 Razors. In portuguese - (Duas Lâminas)

Reason: I stayed many days with out providing feedbacks. I want to give more time for you .

Target Market(s)

Mans ( for woman we will design other package )

Requirements
Nice to have
• maybe some tears as a wet surface...
pls can feel free

```html
<!DOCTYPE html>
<html lang="pt-BR">
<head>
<meta charset="UTF-8">
<title>VELUMOR – Disposable Razor Pack</title>
<link rel="stylesheet" href="https://fonts.googleapis.com/css2?family=Exo+2:ital,wght@0,800;1,700;1,800&display=swap">
<style>
  :root {
    --navy-deep: #03113a;
    --navy: #0a2a7a;
    --blue-mid: #1e6ee0;
    --blue-bright: #2f86ee;
    --blue-soft: #7cc4ff;
    --blue-pale: #a9dcff;
    --silver-light: #eef1f5;
    --silver-dark: #8a939e;
    --window: #ffffff;
    --ink-light: #ffffff;
    --ink-shadow: rgba(3, 17, 58, 0.85);
  }
  html, body {
    margin: 0;
    padding: 0;
    overflow: hidden;
    background: #ffffff;
  }
  .pack {
    position: relative;
    width: 1200px;
    height: 2880px;
    overflow: hidden;
    font-family: "Exo 2", "Arial", sans-serif;
  }
  .pack-art {
    position: absolute;
    inset: 0;
    width: 1200px;
    height: 2880px;
  }
  .brand-name {
    position: absolute;
    top: 150px;
    left: 0;
    width: 1200px;
    margin: 0;
    text-align: center;
    font-weight: 800;
    font-style: normal;
    font-size: 170px;
    letter-spacing: 6px;
    line-height: 1;
    color: var(--ink-light);
  }
  .feature-tag {
    position: absolute;
    right: 36px;
    margin: 0;
    text-align: right;
    font-style: italic;
    font-weight: 700;
    font-size: 52px;
    line-height: 1.12;
    color: var(--ink-light);
    text-shadow: 3px 3px 0 var(--ink-shadow);
  }
  .feature-tag--grip { top: 2385px; }
  .feature-tag--blades { top: 2600px; }
  .unit-count {
    position: absolute;
    left: 90px;
    bottom: 60px;
    display: flex;
    align-items: flex-end;
    color: var(--ink-light);
    font-style: italic;
    font-weight: 800;
    text-shadow: 3px 3px 0 var(--ink-shadow);
  }
  .unit-count__number {
    font-size: 210px;
    line-height: 0.8;
    margin-right: 10px;
  }
  .unit-count__label {
    font-size: 62px;
    line-height: 1.02;
    font-weight: 700;
  }
</style>
</head>
<body>
<main class="pack">
  <svg class="pack-art" viewBox="0 0 1200 2880" xmlns="http://www.w3.org/2000/svg" aria-hidden="true">
    <defs>
      <radialGradient id="bgGlow" cx="0.95" cy="0.55" r="0.75">
        <stop offset="0" stop-color="#1f66d8"/>
        <stop offset="0.55" stop-color="#0a2a7a"/>
        <stop offset="1" stop-color="#03113a"/>
      </radialGradient>
      <linearGradient id="silverBand" x1="0" y1="0" x2="1" y2="1">
        <stop offset="0" stop-color="#eef1f5"/>
        <stop offset="0.5" stop-color="#c4cad2"/>
        <stop offset="1" stop-color="#8a939e"/>
      </linearGradient>
      <linearGradient id="tagSilver" x1="0" y1="0" x2="0" y2="1">
        <stop offset="0" stop-color="#f4f6f8"/>
        <stop offset="0.5" stop-color="#b9c0c8"/>
        <stop offset="1" stop-color="#7f8892"/>
      </linearGradient>
      <path id="windowShape" d="M-200,1100 C250,800 750,600 1190,540 L1100,1000 L800,1560 L520,1960 L-200,2900 Z"/>
    </defs>

    <rect class="pack-background" width="1200" height="2880" fill="url(#bgGlow)"/>

    <g class="window-bands">
      <use href="#windowShape" transform="translate(220,-200)" fill="#1d5fd6" opacity="0.7"/>
      <use href="#windowShape" transform="translate(170,-150)" fill="#7cc4ff"/>
      <use href="#windowShape" transform="translate(140,-122)" fill="#2f86ee"/>
      <use href="#windowShape" transform="translate(105,-92)" fill="#a9dcff"/>
      <use href="#windowShape" transform="translate(75,-66)" fill="#1e6ee0"/>
      <use href="#windowShape" transform="translate(38,-34)" fill="url(#silverBand)"/>
    </g>
    <use class="product-window" href="#windowShape" fill="#ffffff"/>

    <g class="feature-plates">
      <polygon points="500,2360 1200,2360 1200,2530 440,2530" fill="url(#tagSilver)"/>
      <polygon points="560,2570 1200,2570 1200,2770 480,2770" fill="url(#tagSilver)"/>
    </g>
  </svg>

  <h1 class="brand-name">VELUMOR</h1>

  <p class="feature-tag feature-tag--grip">Handle With Grip<br>Cabo Aderente</p>
  <p class="feature-tag feature-tag--blades">2 Razors<br>Duas Laminas</p>

  <div class="unit-count">
    <span class="unit-count__number">5</span>
    <span class="unit-count__label">Units<br>Aparelhos</span>
  </div>
</main>
</body>
</html>
```